1 Dimensional cover for digital product

Please note that if a designer comes in with an original design and other designers try to copy them too closely I will always work with the original designer in order to get the actual look I want.
Therefore it is in the interests of the designers to get their concepts in first.

I am designing some audio products for football (soccer players).

I would like a square version and a 16:9 version of the packaging completed. The square version will be for the Sonvia audio cover and the 16:9 for the thumbnails of videos.

I would like the final images in PSP files as a template that I can change the title and the main image.

I am open to creativity in this project but would like it to be a luxury and premium in what it is portraying.

I have added my logo and also the packaging that I currently use on my sister website which is not aimed at football, soccer.

I've also included an image of one of my models. This would NOT be the product image, but it could be a background image, or you may choose to leave it out altogether.

I've also included an example image as the main product image.

Although I have chosen greyscale I would also like to see products with colour.

The product page is at https://kelvarn.global/collections/all
I add this so that you can chose any one of the titles for this template

Target Market(s)

This is aimed at professional footballers

Industry/Entity Type

Sporting Good

Font styles to use
Serif
Sans Serif

Colors

Designer to choose colors to be used in the design.

Requirements
Must have
• This must look like it is made for an affluent market.
• It may also be simple in its design but I do not wish to be too prescriptive with creativity.
• My typography is Montserrat
Nice to have
• Can include the colors of my logos:
• #5BA9DE
• #272B5F
• Or you can choose to go with greyscale
Should not have
• This is a product for serious athletes so it should look very professional and adult orientated (so not cartoonish its look)

```html
<!DOCTYPE html>
<html lang="en">
<head>
<meta charset="utf-8">
<title>After Game – Hypnosis Sessions</title>
<link rel="stylesheet" href="https://fonts.googleapis.com/css2?family=Montserrat:wght@400;500;600;700&display=swap">
<style>
  :root {
    --ink-black: #050505;
    --panel-grey: #c0c1c3;
    --band-dark: #1a1a1b;
    --band-light: #5a5a5c;
    --brand-blue: #5ba9de;
    --brand-navy: #272b5f;
    --accent-gold: #b3a66b;
    --text-white: #ffffff;
  }
  html, body {
    margin: 0;
    padding: 0;
    overflow: hidden;
    background: var(--ink-black);
  }
  .cover {
    position: relative;
    width: 1200px;
    height: 676px;
    overflow: hidden;
    background: var(--ink-black);
    font-family: "Montserrat", Arial, sans-serif;
  }
  .cover__backdrop {
    position: absolute;
    inset: 0;
    width: 1200px;
    height: 676px;
  }
  .cover__athlete-photo {
    position: absolute;
    left: 680px;
    top: 76px;
    width: 400px;
    height: 600px;
    background: radial-gradient(ellipse at 50% 40%, #5b5b5d 0%, #333334 45%, rgba(10,10,10,0) 75%);
  }
  .brand {
    position: absolute;
    left: 42px;
    top: 26px;
    width: 170px;
    text-align: center;
    color: var(--brand-navy);
  }
  .brand__dot {
    display: block;
    width: 36px;
    height: 36px;
    margin: 0 auto 12px;
    border-radius: 50%;
    background: var(--brand-navy);
  }
  .brand__name {
    display: block;
    font-size: 8.6px;
    font-weight: 500;
    letter-spacing: 0.2px;
    line-height: 1.3;
    white-space: nowrap;
  }
  .brand__product {
    display: block;
    font-size: 13px;
    font-weight: 500;
    letter-spacing: 1px;
    line-height: 1.3;
  }
  .series-label {
    position: absolute;
    left: 249px;
    top: 226px;
    margin: 0;
    font-size: 20px;
    font-weight: 500;
    color: var(--brand-blue);
  }
  .title {
    position: absolute;
    left: 200px;
    top: 258px;
    width: 476px;
    margin: 0;
    text-align: right;
    font-size: 131px;
    font-weight: 700;
    line-height: 103px;
    letter-spacing: -2px;
    color: var(--brand-blue);
  }
  .title__line { display: block; }
  .tagline {
    position: absolute;
    left: 295px;
    top: 511px;
    margin: 0;
    font-size: 14.3px;
    font-weight: 400;
    color: var(--text-white);
    white-space: nowrap;
  }
  .tagline__marker {
    position: absolute;
    left: 242px;
    top: 505px;
    width: 24px;
    height: 24px;
    background: var(--accent-gold);
    transform: rotate(45deg);
  }
</style>
</head>
<body>
  <main class="cover">
    <svg class="cover__backdrop" viewBox="0 0 1200 676" aria-hidden="true">
      <defs>
        <linearGradient id="band-shade" x1="0" y1="1" x2="0.6" y2="0.2">
          <stop offset="0" stop-color="var(--band-light)"/>
          <stop offset="0.35" stop-color="#2b2b2c"/>
          <stop offset="1" stop-color="var(--band-dark)"/>
        </linearGradient>
      </defs>
      <polygon class="backdrop__diagonal-band" points="344,0 778,0 102,676 0,676 0,344" fill="url(#band-shade)"/>
      <polygon class="backdrop__corner-panel" points="0,0 344,0 0,344" fill="var(--panel-grey)"/>
    </svg>

    <div class="cover__athlete-photo" role="img" aria-label="Black-and-white portrait of a young footballer in a training top, crouching with hands clasped, against a dark background with soft floating light particles"></div>

    <div class="brand">
      <span class="brand__dot"></span>
      <span class="brand__name">ELIAN MARSH HYPNOTHERAPY</span>
      <span class="brand__product">KELVARN</span>
    </div>

    <p class="series-label">Hypnosis sessions</p>
    <h1 class="title">
      <span class="title__line">AFTER</span>
      <span class="title__line">GAME</span>
    </h1>

    <span class="tagline__marker"></span>
    <p class="tagline">CONDITIONING YOU TOWARDS EVEN BETTER FUTURE PERFORMANCES.</p>
  </main>
</body>
</html>
```